Maplecrest Disability - Social Security Disability Attorneys

Our company is expanding to attract clients nationwide for our social security disability practice. We have a logo, but I am looking for a creative and elegant letterhead that projects an image of being technologically advanced but still professional enough for the legal field. I am looking for the "wow factor" combined with this is still professional enough for a law practice.

Requesting letterhead and business card design
Updates

Had to update and change the logo. The previous logo had a typo. Please send updates with the new logo for consideration. The letterhead and business cards should be professional enough to be used for a law firm. Thanks.

Industry/Entity Type

Law Practice, Law Firm, Healthcare Industry, Government

Colors

Designer to choose colors to be used in the design.

Requirements
Nice to have
• **Please create a vertical design for the business card**

```html
<!DOCTYPE html>
<html lang="en">
<head>
<meta charset="utf-8">
<title>Maplecrest Disability – Stationery</title>
<link href="https://fonts.googleapis.com/css2?family=Lato:wght@400;700&family=Roboto:wght@400;700&family=Great+Vibes&display=swap" rel="stylesheet">
<style>
  :root {
    --blue: #4468d6;
    --blue-card: #5871b9;
    --blue-card-light: #6a82c6;
    --orange: #ef7f2a;
    --ink: #222;
    --paper: #fff;
    --stage: #b9b9bb;
  }
  * { margin: 0; padding: 0; box-sizing: border-box; }
  html, body { width: 1200px; height: 848px; overflow: hidden; }
  body { background: var(--stage); position: relative; font-family: 'Lato', sans-serif; color: var(--ink); }

  .sheet { position: absolute; background: var(--paper); overflow: hidden; }
  .abs { position: absolute; }

  /* Letterhead */
  .letterhead { left: 151px; top: 118px; width: 455px; height: 623px; }
  .brand-dot { position: absolute; width: 8px; height: 8px; border-radius: 50%; background: var(--orange); }
  .brand-name { position: absolute; font-family: 'Lato', sans-serif; font-weight: 400; color: var(--blue); text-transform: uppercase; white-space: nowrap; }
  .brand-tag { position: absolute; font-family: 'Lato', sans-serif; font-weight: 400; color: var(--blue); text-transform: uppercase; white-space: nowrap; }

  .letterhead .brand-dot { left: 91px; top: 43px; }
  .letterhead .brand-name { left: 25px; top: 58px; width: 141px; text-align: center; font-size: 11.5px; letter-spacing: 1.1px; }
  .letterhead .brand-tag { left: 25px; top: 72px; width: 141px; text-align: center; font-size: 4px; letter-spacing: 0.9px; }

  .contact-block { left: 321px; top: 36px; width: 110px; height: 51px; border-left: 1px solid var(--orange); padding-left: 6px; font-family: 'Roboto', sans-serif; font-size: 6.8px; line-height: 10.3px; }
  .contact-block .addr { margin-top: 1px; margin-bottom: 2px; }
  .contact-line { display: flex; align-items: center; gap: 5px; height: 10.4px; }
  .contact-line svg { width: 7px; height: 7px; flex: none; }

  .letter { left: 25px; top: 148px; width: 405px; font-size: 8.6px; line-height: 10.2px; }
  .letter .date { font-size: 9.3px; margin-bottom: 10px; }
  .letter .block { margin-bottom: 10px; font-size: 8.6px; }
  .letter .salutation { font-size: 11px; font-weight: 700; margin: 2px 0 9px; }
  .letter p.body { text-align: justify; margin-bottom: 9.5px; }
  .letter .regards { margin-top: 18px; }
  .letter .signature { font-family: 'Great Vibes', cursive; font-size: 22px; margin-top: 8px; line-height: 24px; }

  .wave { position: absolute; left: 0; bottom: 0; display: block; }

  /* Business card front */
  .card-front { left: 627px; top: 234px; width: 213px; height: 372px; text-align: center; font-family: 'Roboto', sans-serif; }
  .card-front .brand-dot { left: 102px; top: 54px; }
  .card-front .brand-name { left: 0; width: 213px; top: 76px; font-size: 12.5px; letter-spacing: 1.2px; }
  .card-front .brand-tag { left: 0; width: 213px; top: 92px; font-size: 4.2px; letter-spacing: 1px; }
  .holder-name { position: absolute; left: 0; width: 213px; top: 123px; font-size: 12.5px; font-weight: 700; color: var(--orange); text-transform: uppercase; }
  .holder-role { position: absolute; left: 50px; width: 113px; top: 142px; font-size: 9.5px; display: flex; align-items: center; gap: 3px; }
  .holder-role::before, .holder-role::after { content: ""; flex: 1; height: 1px; background: var(--orange); }
  .card-address { position: absolute; left: 0; width: 213px; top: 191px; font-size: 8.6px; line-height: 12.5px; }
  .card-icons { position: absolute; left: 0; width: 213px; top: 233px; display: flex; justify-content: center; gap: 17px; }
  .card-icons svg { width: 9px; height: 9px; }
  .card-contacts { position: absolute; left: 0; width: 213px; top: 259px; font-size: 8.8px; line-height: 14px; }

  /* Business card back */
  .card-back { left: 864px; top: 234px; width: 213px; height: 372px; background: var(--blue-card); color: #fff; text-align: center; font-family: 'Roboto', sans-serif; }
  .facet-field { position: absolute; inset: 0; background: linear-gradient(160deg, #5570b5 0%, #5c77bf 40%, var(--blue-card-light) 62%, #5872b8 100%); }
  .card-back .brand-dot { left: 102px; top: 65px; background: #fff; }
  .card-back .brand-name { left: 0; width: 213px; top: 85px; font-size: 11.5px; letter-spacing: 1.1px; color: #fff; }
  .card-back .brand-tag { left: 0; width: 213px; top: 99px; font-size: 3.8px; letter-spacing: 0.9px; color: #fff; }
  .sectors { position: absolute; left: 0; width: 213px; top: 317px; font-size: 8.5px; line-height: 12.5px; }
</style>
</head>
<body>

<section class="sheet letterhead" aria-label="Letterhead">
  <span class="brand-dot"></span>
  <div class="brand-name">Maplecrest Disability</div>
  <div class="brand-tag">Social Security Disability Attorneys</div>

  <div class="abs contact-block">
    <div class="addr">Suite 4,level 12,Harbour<br>Street Sydney NSW 2000</div>
    <div class="contact-line">
      <svg viewBox="0 0 10 10"><path d="M2 1 L4 3 L3 4.2 Q4.3 6 5.8 7 L7 6 L9 8 L7.8 9.2 Q4 9 0.8 2.2 Z" fill="var(--orange)"/></svg>
      614-555-0193
    </div>
    <div class="contact-line">
      <svg viewBox="0 0 10 10"><rect x="0.5" y="2" width="9" height="6.5" fill="var(--orange)"/><path d="M0.5 2 L5 5.8 L9.5 2" stroke="#fff" stroke-width="0.8" fill="none"/></svg>
      Info@maplecrestdisability.com
    </div>
    <div class="contact-line">
      <svg viewBox="0 0 10 10"><circle cx="5" cy="5" r="4.5" fill="var(--orange)"/><path d="M0.5 5 H9.5 M5 0.5 V9.5" stroke="#fff" stroke-width="0.6"/></svg>
      www.maplecrestdisability.com
    </div>
  </div>

  <div class="abs letter">
    <div class="date">January-03-2020</div>
    <div class="block">Mr, Alan Reeve<br>President</div>
    <div class="block">Brightline Group<br>123 Street Name, Suite# 10<br>City, State, 120023</div>
    <div class="salutation">Dear Mr, Alan</div>
    <p class="body">Lorem ipsum dolor sit amet, consectetur adipisicing elit, sed do eiusmod tempor incididunt ut labore et dolore magna aliqua. Ut enim ad minim veniam, quis nostrud exercitation ullamco laboris nisi ut aliquip ex ea commodo consequat. Duis aute irure dolor in reprehenderit in voluptate velit esse cillum dolore eu fugiat nulla pariatur.</p>
    <p class="body">Lorem ipsum dolor sit amet, consectetur adipisicing elit, sed do eiusmod tempor incididunt ut labore et dolore magna aliqua. Ut enim ad minim veniam, quis nostrud exercitation ullamco laboris nisi ut aliquip ex ea commodo consequat. Duis aute irure dolor in reprehenderit in voluptate velit esse cillum dolore eu fugiat nulla pariatur.</p>
    <p class="body">Lorem ipsum dolor sit amet, consectetur adipisicing elit, sed do eiusmod tempor incididunt ut labore et dolore magna aliqua. Ut enim ad minim veniam, quis nostrud exercitation ullamco laboris nisi ut aliquip ex ea commodo consequat.</p>
    <p class="body">Excepteur sint occaecat cupidatat non proident, sunt in culpa qui officia deserunt mollit anim id est laborum. re et dolore magnam aliquam quaerat voluptatem.</p>
    <div class="regards">Regards</div>
    <div class="signature">Peter Hale</div>
  </div>

  <svg class="wave" width="455" height="140" viewBox="0 0 455 140" aria-hidden="true">
    <path d="M0 80 C40 60 80 50 120 55 C200 64 300 108 365 103 C415 99 440 80 455 62 L455 71 C437 97 410 111 360 112 C290 113 200 71 120 64 C80 61 40 75 0 90 Z" fill="var(--orange)"/>
    <path d="M0 106 C40 85 80 76 120 79 C200 86 290 127 360 126 C410 125 440 104 455 86 L455 140 L0 140 Z" fill="var(--blue)"/>
  </svg>
</section>

<section class="sheet card-front" aria-label="Business card front">
  <span class="brand-dot"></span>
  <div class="brand-name">Maplecrest Disability</div>
  <div class="brand-tag">Social Security Disability Attorneys</div>

  <div class="holder-name">Darren Whitcombe</div>
  <div class="holder-role">Co-Founder</div>

  <div class="card-address">Suite 4,level 12,Harbour<br>Street Sydney NSW 2000</div>

  <div class="card-icons" aria-hidden="true">
    <svg viewBox="0 0 10 10"><path d="M2 1 L4 3 L3 4.2 Q4.3 6 5.8 7 L7 6 L9 8 L7.8 9.2 Q4 9 0.8 2.2 Z" fill="var(--orange)"/></svg>
    <svg viewBox="0 0 10 10"><rect x="0.5" y="2" width="9" height="6.5" fill="var(--orange)"/><path d="M0.5 2 L5 5.8 L9.5 2" stroke="#fff" stroke-width="0.8" fill="none"/></svg>
    <svg viewBox="0 0 10 10"><circle cx="5" cy="5" r="4.5" fill="var(--orange)"/><path d="M0.5 5 H9.5 M5 0.5 V9.5" stroke="#fff" stroke-width="0.6"/></svg>
  </div>

  <div class="card-contacts">614-555-0193<br>Info@maplecrestdisability.com<br>www.maplecrestdisability.com</div>

  <svg class="wave" width="213" height="52" viewBox="0 0 213 52" aria-hidden="true">
    <path d="M0 24 C40 32 80 24 120 14 C150 8 175 10 204 20 L201 22 C175 14 150 13 120 19 C80 28 40 37 0 28 Z" fill="var(--orange)"/>
    <path d="M0 32 C40 40 80 30 120 21 C150 15 180 15 213 27 L213 52 L0 52 Z" fill="var(--blue-card)"/>
  </svg>
</section>

<section class="sheet card-back" aria-label="Business card back">
  <div class="facet-field" role="img" aria-label="Soft blue faceted background"></div>
  <span class="brand-dot"></span>
  <div class="brand-name">Maplecrest Disability</div>
  <div class="brand-tag">Social Security Disability Attorneys</div>
  <div class="sectors">Law Practice, Law Firm,<br>Healthcare Industry, Government</div>
</section>

</body>
</html>
```